Bright Harbor Counseling Letterhead for hip modern business

I would like some ombre use of the colors in the logo hip letterhead that incorporates logo colors and feel, needs to connect with young professionals and college students. i need to be able to write letters to schools to excuse absences as well. i like color blocks on one side preferably using colors from the attached logo design.

Target Market(s)

high income young people, young adults and college students

Industry/Entity Type

mental health

Font styles to use
Serif
Sans Serif

Colors
0054AA
0677BA
7BADD7
CADEEF
E8F1F8
0094D4
00A9DD
6FCCEA
C7EBF8
E9F6FB
00AB8E
00BBA5
67D7C9
C6EFE9
E9F9F6
59FF00
82FF00
B8FF75
E3FFCB
F4FFEA
A7469A
B969AE
D3A5CF
EDDBEB
F8F0F9
6B429C
8869AF
B7A5CE
E3DAEB
F3F0F8

Requirements
Must have
• a modern hip feel, somewhat color

```html
<!DOCTYPE html>
<html lang="en">
<head>
<meta charset="utf-8">
<title>Bright Harbor Counseling – Letterhead</title>
<link rel="stylesheet" href="https://fonts.googleapis.com/css2?family=Open+Sans:wght@300;600;700&display=swap">
<style>
  :root {
    --backdrop: #d9dcdd;
    --paper: #ffffff;
    --purple: #8a3f9a;
    --violet: #6b429c;
    --teal: #3fb3c4;
    --rule-grey: #9a9a9a;
    --ink: #5a5a5a;
    --logo-ink: #4a4a4a;
  }
  * { margin: 0; padding: 0; box-sizing: border-box; }
  html, body {
    width: 1200px; height: 784px; overflow: hidden;
    background: var(--backdrop);
    font-family: "Open Sans", Arial, sans-serif;
  }
  .letterhead {
    position: absolute;
    left: 320px; top: 30px;
    width: 560px; height: 724px;
    background: var(--paper);
    box-shadow: 0 6px 18px rgba(0,0,0,0.18);
    overflow: hidden;
  }
  .header-rule { position: absolute; }
  .header-rule--short { left: 0; top: 30px; }
  .header-rule--long { left: 262px; top: 30px; }
  .brand {
    position: absolute; left: 58px; top: 14px;
    display: flex; align-items: center; gap: 12px;
    color: var(--logo-ink); font-weight: 300;
  }
  .brand__name { line-height: 1; }
  .brand__title { display: block; font-size: 21px; letter-spacing: 0.3px; }
  .brand__sub { display: block; font-size: 11px; letter-spacing: 3px; margin-top: 4px; text-align: right; }
  .brand__dot { width: 30px; height: 30px; border-radius: 50%; background: var(--purple); }
  .footer-art { position: absolute; left: 0; bottom: 0; }
  .contact {
    position: absolute; left: 12px; bottom: 34px;
    display: flex; gap: 8px; align-items: center;
    font-size: 7.4px; font-weight: 700; color: var(--ink); white-space: nowrap;
  }
  .contact__item { display: flex; align-items: center; gap: 3px; }
  .contact__icon { width: 9px; height: 9px; }
  .web {
    position: absolute; right: 16px; bottom: 8px;
    font-size: 13px; font-weight: 700; color: #fff; letter-spacing: 0.2px;
  }
</style>
</head>
<body>
  <section class="letterhead" aria-label="Bright Harbor Counseling letterhead">
    <svg class="header-rule header-rule--short" width="44" height="12" viewBox="0 0 44 12">
      <rect x="0" y="0" width="44" height="3" fill="var(--teal)"/>
      <rect x="0" y="4" width="44" height="8" fill="var(--purple)"/>
    </svg>

    <div class="brand">
      <div class="brand__name">
        <span class="brand__title">Bright Harbor</span>
        <span class="brand__sub">Counseling</span>
      </div>
      <span class="brand__dot" aria-hidden="true"></span>
    </div>

    <svg class="header-rule header-rule--long" width="274" height="12" viewBox="0 0 274 12">
      <rect x="0" y="0" width="274" height="3" fill="var(--teal)"/>
      <rect x="0" y="4" width="274" height="8" fill="var(--purple)"/>
    </svg>

    <svg class="footer-art" width="560" height="60" viewBox="0 0 560 60" aria-hidden="true">
      <defs>
        <linearGradient id="webBand" x1="0" y1="1" x2="1" y2="0">
          <stop offset="0" stop-color="var(--violet)"/>
          <stop offset="0.55" stop-color="var(--purple)"/>
          <stop offset="1" stop-color="var(--teal)"/>
        </linearGradient>
      </defs>
      <polyline points="0,40 150,40 156,36 262,36 268,32 378,32" fill="none" stroke="var(--rule-grey)" stroke-width="1.5"/>
      <rect x="0" y="44" width="380" height="3" fill="var(--teal)"/>
      <rect x="0" y="48" width="380" height="12" fill="var(--purple)"/>
      <polygon points="386,26 560,26 560,60 376,60" fill="url(#webBand)"/>
    </svg>

    <div class="contact">
      <span class="contact__item">
        <svg class="contact__icon" viewBox="0 0 10 10"><circle cx="5" cy="5" r="5" fill="var(--purple)"/><path d="M5 2.2a1.8 1.8 0 0 1 1.8 1.8C6.8 5.4 5 7.8 5 7.8S3.2 5.4 3.2 4A1.8 1.8 0 0 1 5 2.2z" fill="#fff"/></svg>
        48 Lantern Row, Unit 7, Marlow Bay, 55210
      </span>
      <span class="contact__item">
        <svg class="contact__icon" viewBox="0 0 10 10"><circle cx="5" cy="5" r="5" fill="var(--purple)"/><rect x="3.6" y="2.2" width="2.8" height="5.6" rx="0.6" fill="#fff"/></svg>
        (000) 000-0000
      </span>
      <span class="contact__item">
        <svg class="contact__icon" viewBox="0 0 10 10"><circle cx="5" cy="5" r="5" fill="var(--purple)"/><rect x="2.6" y="3" width="4.8" height="4" fill="#fff"/></svg>
        (000) 000-0000
      </span>
      <span class="contact__item">
        <svg class="contact__icon" viewBox="0 0 10 10"><circle cx="5" cy="5" r="5" fill="var(--purple)"/><rect x="2.5" y="3.2" width="5" height="3.6" fill="#fff"/><path d="M2.5 3.2 5 5.2 7.5 3.2" fill="none" stroke="var(--purple)" stroke-width="0.6"/></svg>
        info@brightharbor.com
      </span>
    </div>

    <div class="web">www.brightharbor.com</div>
  </section>
</body>
</html>
```